Business Card Design for Property Development Company Director

I am looking for a professional and unforgettable business card design for our Director of our Property Development Company.
Please see attached .pptx file to find out what information to include. You don't have to follow the exact format shown in the file - I am interested to see your creative flair using the information provided.

```html
<!DOCTYPE html>
<html lang="en">
<head>
<meta charset="utf-8">
<title>Kestrel Property Group – Business Card</title>
<link rel="stylesheet" href="https://fonts.googleapis.com/css2?family=Montserrat:wght@400;500;700;800&display=swap">
<style>
  :root {
    --stage: #3a3a3a;
    --ink-black: #0a0a0a;
    --brand-blue: #0c4f9c;
    --mid-grey: #5c5c5c;
    --panel-grey: #e2e2e2;
    --paper: #f7f7f7;
    --text-grey: #555555;
    --white: #ffffff;
  }
  * { box-sizing: border-box; margin: 0; padding: 0; }
  html, body { width: 1200px; height: 1021px; overflow: hidden; }
  body {
    background: var(--stage);
    font-family: "Montserrat", sans-serif;
    position: relative;
  }
  .card {
    position: absolute;
    width: 580px;
    height: 352px;
    overflow: hidden;
    box-shadow: 0 10px 30px rgba(0,0,0,.45);
  }

  /* Back of card */
  .card-back { left: 570px; top: 90px; background: var(--ink-black); color: var(--white); }
  .card-back .accent { position: absolute; inset: 0; }
  .card-back .tagline {
    position: absolute; right: 40px; top: 50px;
    text-align: right; font-size: 14px; line-height: 1.35; font-weight: 500;
  }
  .card-back .brand {
    position: absolute; right: 40px; top: 150px;
    display: flex; align-items: center; gap: 12px;
  }
  .card-back .pitch {
    position: absolute; right: 40px; bottom: 42px;
    text-align: right; font-size: 14px; line-height: 1.45;
  }
  .card-back .pitch strong { font-weight: 800; letter-spacing: .02em; }

  .brand-mark { width: 30px; height: 30px; background: var(--brand-blue); flex: none; }
  .brand-name {
    font-weight: 800; font-size: 24px; letter-spacing: .03em;
    text-transform: uppercase; color: var(--brand-blue);
  }
  .card-back .brand-name { color: var(--white); }
  .card-back .brand-mark { background: var(--white); }

  /* Front of card */
  .card-front { left: 60px; top: 520px; background: var(--paper); }
  .card-front .side-panel { position: absolute; right: 0; top: 0; width: 190px; height: 100%; background: var(--panel-grey); }
  .card-front .side-bar { position: absolute; left: 0; top: 140px; width: 14px; height: 140px; background: var(--brand-blue); }
  .card-front .brand { position: absolute; left: 44px; top: 40px; display: flex; align-items: center; gap: 12px; }
  .card-front .person { position: absolute; left: 44px; top: 140px; }
  .person .name { font-size: 20px; font-weight: 800; color: var(--brand-blue); }
  .person .role { font-size: 15px; color: var(--text-grey); margin-top: 2px; }
  .contact { list-style: none; margin-top: 22px; font-size: 15px; color: var(--text-grey); }
  .contact li { display: flex; align-items: center; gap: 10px; line-height: 1.55; }
  .contact svg { width: 14px; height: 14px; fill: var(--brand-blue); flex: none; }
  .licence { font-size: 15px; color: var(--text-grey); margin-top: 6px; }
</style>
</head>
<body>

<section class="card card-back" aria-label="Card back">
  <svg class="accent" viewBox="0 0 580 352" preserveAspectRatio="none" aria-hidden="true">
    <polygon points="0,0 70,0 70,352 0,352" fill="var(--mid-grey)"/>
    <polygon points="110,0 210,0 290,352 190,352" fill="var(--brand-blue)"/>
  </svg>
  <p class="tagline">Property Development<br>&amp; Site Acquisition Specialists</p>
  <div class="brand">
    <span class="brand-mark"></span>
    <span class="brand-name">Kestrel Property Group</span>
  </div>
  <p class="pitch">Ask me about our<br><strong>INVESTMENT &amp; PARTNERSHIP</strong> opportunities</p>
</section>

<section class="card card-front" aria-label="Card front">
  <div class="side-panel"></div>
  <div class="side-bar"></div>
  <div class="brand">
    <span class="brand-mark"></span>
    <span class="brand-name">Kestrel Property Group</span>
  </div>
  <div class="person">
    <p class="name">Daniel Mercer</p>
    <p class="role">Director</p>
    <ul class="contact">
      <li><svg viewBox="0 0 24 24"><path d="M6.6 10.8a15 15 0 0 0 6.6 6.6l2.2-2.2a1 1 0 0 1 1-.25 11.4 11.4 0 0 0 3.6.57 1 1 0 0 1 1 1V20a1 1 0 0 1-1 1A17 17 0 0 1 3 4a1 1 0 0 1 1-1h3.5a1 1 0 0 1 1 1c0 1.25.2 2.45.57 3.57a1 1 0 0 1-.25 1z"/></svg>0400 218 365</li>
      <li><svg viewBox="0 0 24 24"><path d="M2 5h20v14H2zm2 2v.5l8 5 8-5V7zm0 2.8V17h16V9.8l-8 5z"/></svg>daniel@kestrelpg.com.au</li>
      <li><svg viewBox="0 0 24 24"><path d="M12 2a10 10 0 1 0 0 20 10 10 0 0 0 0-20zm0 2c.9 0 2.2 1.8 2.8 5H9.2C9.8 5.8 11.1 4 12 4zM4.3 11h4.7a20 20 0 0 0 0 2H4.3a8 8 0 0 1 0-2zm10.7 0h4.7a8 8 0 0 1 0 2H15a20 20 0 0 0 0-2zm-5.8 4h5.6c-.6 3.2-1.9 5-2.8 5s-2.2-1.8-2.8-5z"/></svg>www.kestrelpg.com.au</li>
    </ul>
    <p class="licence">Real Estate Lic: 5512093 &amp; 5512094</p>
  </div>
</section>

</body>
</html>
```